Business Card and Letterhead for Pimlu - modern real estate business

I need a double sided business card design for Pimlu. Please see business card brief here https://files.trelvonadocs.com/sheet/r/7QzTmWbaXLJnoPEd-kRyUgFhHsstbvCe2qfoMxDa_pz/view?mode=shared

Please feel free to design the business cards however you feel best. I am happy to give some creative freedoms and then provide feedback from there.

Please then also create a letterhead to match the business card design

Colors

Designer to choose colors to be used in the design.

Requirements
Must have
• Must be a modern, elegant business card which looks very professional

```html
<!DOCTYPE html>
<html lang="en">
<head>
<meta charset="utf-8">
<title>Pimlu Business Card</title>
<link href="https://fonts.googleapis.com/css2?family=Montserrat:wght@400;500;600&display=swap" rel="stylesheet">
<style>
  :root {
    --backdrop: #2a2a2a;
    --card-black: #050505;
    --stripe: #262626;
    --brand-red: #e0202a;
    --ink: #1e1e1e;
    --paper: #ffffff;
    --photo-dark: #3a3f3c;
    --photo-mid: #6f7a72;
    --photo-light: #a9b0ab;
  }
  * { box-sizing: border-box; margin: 0; padding: 0; }
  html, body { width: 1200px; height: 900px; overflow: hidden; }
  body {
    background: var(--backdrop);
    font-family: "Montserrat", sans-serif;
    position: relative;
  }
  .card {
    position: absolute;
    left: 250px;
    width: 700px;
    height: 400px;
    overflow: hidden;
    box-shadow: 0 10px 30px rgba(0,0,0,0.45);
  }
  /* Front */
  .card-front { top: 40px; background: var(--card-black); }
  .front-stripes { position: absolute; inset: 0; }
  .front-wordmark {
    position: absolute;
    left: 0; right: 0; top: 130px;
    text-align: center;
    color: var(--brand-red);
    font-weight: 600;
    font-size: 112px;
    letter-spacing: 10px;
  }
  .front-url {
    position: absolute;
    left: 0; right: 0; bottom: 42px;
    text-align: center;
    color: var(--paper);
    font-size: 17px;
    letter-spacing: 1.5px;
  }
  .front-url .accent { color: var(--brand-red); font-weight: 600; }
  /* Back */
  .card-back { top: 460px; background: var(--paper); }
  .portrait-area {
    position: absolute;
    left: 0; top: 0; width: 700px; height: 215px;
    background:
      radial-gradient(ellipse at 55% 30%, var(--photo-light) 0%, rgba(169,176,171,0) 45%),
      linear-gradient(90deg, var(--photo-dark) 0%, var(--photo-mid) 50%, var(--photo-dark) 100%);
  }
  .back-wordmark {
    position: absolute;
    right: 34px; top: 140px;
    color: var(--brand-red);
    font-weight: 600;
    font-size: 46px;
    letter-spacing: 4px;
  }
  .divider {
    position: absolute;
    left: 0; top: 215px; width: 700px; height: 3px;
    background: var(--brand-red);
  }
  .name-marker {
    position: absolute;
    left: 0; top: 240px; width: 9px; height: 40px;
    background: var(--brand-red);
  }
  .agent-name {
    position: absolute;
    left: 30px; top: 236px;
    color: var(--brand-red);
    font-weight: 500;
    font-size: 28px;
    letter-spacing: 1px;
    text-transform: uppercase;
  }
  .agent-title {
    position: absolute;
    left: 30px; top: 272px;
    color: var(--ink);
    font-size: 18px;
  }
  .contact-block {
    position: absolute;
    right: 34px; top: 250px;
    text-align: right;
    color: var(--ink);
    font-size: 18px;
    line-height: 1.3;
  }
  .address { margin-bottom: 10px; padding-right: 36px; }
  .contact-line { display: flex; justify-content: flex-end; align-items: center; gap: 16px; }
  .contact-line svg { width: 20px; height: 20px; }
</style>
</head>
<body>
  <section class="card card-front">
    <svg class="front-stripes" width="700" height="400" viewBox="0 0 700 400" aria-hidden="true">
      <polygon points="140,0 170,0 290,230 260,230" fill="var(--stripe)"/>
      <polygon points="210,0 230,0 320,170 300,170" fill="var(--stripe)"/>
      <polygon points="190,230 215,230 30,400 5,400" fill="var(--stripe)"/>
    </svg>
    <div class="front-wordmark">PIMLU</div>
    <div class="front-url">www.<span class="accent">pimlu</span>.com</div>
  </section>

  <section class="card card-back">
    <div class="portrait-area" role="img" aria-label="Portrait photograph of the agent against an outdoor valley landscape"></div>
    <div class="back-wordmark">PIMLU</div>
    <div class="divider"></div>
    <div class="name-marker"></div>
    <h1 class="agent-name">Dara Whitlock</h1>
    <p class="agent-title">Licenced Real Estate Agent</p>
    <div class="contact-block">
      <p class="address">PO Box 7316<br>Larkvale NSW 2791</p>
      <p class="contact-line">0491 570 318
        <svg viewBox="0 0 24 24" aria-hidden="true"><path d="M6.6 10.8a15 15 0 0 0 6.6 6.6l2.2-2.2a1 1 0 0 1 1-.25 11 11 0 0 0 3.6.6 1 1 0 0 1 1 1V20a1 1 0 0 1-1 1A17 17 0 0 1 3 4a1 1 0 0 1 1-1h3.5a1 1 0 0 1 1 1 11 11 0 0 0 .6 3.6 1 1 0 0 1-.25 1z" fill="var(--brand-red)"/></svg>
      </p>
      <p class="contact-line">dara@pimlu.com
        <svg viewBox="0 0 24 24" aria-hidden="true"><rect x="3" y="5" width="18" height="14" rx="2" fill="none" stroke="var(--brand-red)" stroke-width="2"/><path d="M3 7l9 6 9-6" fill="none" stroke="var(--brand-red)" stroke-width="2"/></svg>
      </p>
      <p class="contact-line">www.pimlu.com
        <svg viewBox="0 0 24 24" aria-hidden="true"><g fill="none" stroke="var(--brand-red)" stroke-width="1.6"><circle cx="12" cy="12" r="9"/><ellipse cx="12" cy="12" rx="4" ry="9"/><path d="M3 12h18M5 7h14M5 17h14"/></g></svg>
      </p>
    </div>
  </section>
</body>
</html>
```